Executive Business Card for Healthcare Company [Need Today]

I need a business card design for a healthcare company. The only branding the company has thus far is a logo. The cards will be utilized by company executives. The design I envision will be vibrant and appealing but with a corporate feel. They shouldn't be too casual or playful. I would like to complete this project TODAY if possible.

Target Market(s)

Healthcare vendors, other executives in healthcare and pharmaceuticals

Industry/Entity Type

Pharmaceutical

Contact Information for Business Card

See attachment

Font styles to use
Serif
Sans Serif

Colors

Designer to choose colors to be used in the design.

```html
<!DOCTYPE html>
<html lang="en">
<head>
<meta charset="utf-8">
<title>Corvane Therapeutics – Business Card</title>
<link href="https://fonts.googleapis.com/css2?family=Roboto:wght@300;400&display=swap" rel="stylesheet">
<style>
  :root {
    --backdrop: #3a3a3c;
    --card: #1d1e20;
    --emboss: #55575a;
    --emboss-text: #7a7c80;
    --teal: #2bb3c6;
    --ring: #3cc0a0;
    --ink: #f1f2f3;
  }
  * { margin: 0; padding: 0; box-sizing: border-box; }
  html, body { width: 799px; height: 1200px; overflow: hidden; }
  body {
    background: var(--backdrop);
    font-family: "Roboto", Arial, sans-serif;
    position: relative;
  }
  .card {
    position: absolute;
    left: 90px;
    width: 620px;
    height: 354px;
    background: var(--card);
    overflow: hidden;
    box-shadow: 0 14px 30px rgba(0,0,0,0.45);
  }
  .card--front { top: 120px; }
  .card--back { top: 725px; }

  /* Front */
  .front-mark {
    position: absolute;
    left: 50px; top: 62px;
    width: 130px; height: 130px;
    border: 2px solid var(--emboss);
    border-radius: 50%;
  }
  .front-divider {
    position: absolute;
    left: 196px; top: 118px;
    width: 1px; height: 50px;
    background: var(--emboss);
  }
  .brand {
    position: absolute;
    font-weight: 300;
    line-height: 1;
    text-align: right;
  }
  .brand__name { display: block; font-size: 60px; letter-spacing: 1px; }
  .brand__sub { display: block; font-size: 34px; margin-top: 2px; }
  .card--front .brand { left: 212px; top: 108px; color: var(--emboss-text); }
  .website {
    position: absolute;
    left: 50px; top: 272px;
    color: var(--ink);
    font-size: 17px;
    letter-spacing: 3px;
  }

  /* Back */
  .ring { position: absolute; left: 0; top: 0; }
  .card--back .brand { right: 60px; top: 44px; color: var(--teal); }
  .card--back .brand__name { font-size: 54px; }
  .card--back .brand__sub { font-size: 30px; }
  .person { position: absolute; left: 318px; top: 140px; }
  .person__name { color: var(--teal); font-size: 25px; font-weight: 400; }
  .person__title { color: var(--ink); font-size: 12px; margin-top: 2px; }
  .contact { list-style: none; margin-top: 12px; color: var(--ink); font-size: 15px; line-height: 21px; }
  .contact li { display: flex; align-items: center; gap: 7px; }
  .contact svg { width: 12px; height: 12px; fill: var(--teal); }
  .contact .plain { padding-left: 0; }
</style>
</head>
<body>
  <section class="card card--front">
    <div class="front-mark"></div>
    <div class="front-divider"></div>
    <div class="brand">
      <span class="brand__name">corvane</span>
      <span class="brand__sub">therapeutics</span>
    </div>
    <p class="website">www.corvanerx.com</p>
  </section>

  <section class="card card--back">
    <svg class="ring" width="300" height="354" viewBox="0 0 300 354" aria-hidden="true">
      <circle cx="110" cy="160" r="165" fill="none" stroke="var(--ring)" stroke-width="10"/>
    </svg>
    <div class="brand">
      <span class="brand__name">corvane</span>
      <span class="brand__sub">therapeutics</span>
    </div>
    <div class="person">
      <h1 class="person__name">Daniel Hartley</h1>
      <p class="person__title">Senior Director of Marketing</p>
      <ul class="contact">
        <li><svg viewBox="0 0 12 12"><path d="M2 1h3l1 3-1.5 1a6 6 0 0 0 2.5 2.5L8 6l3 1v3c0 .6-.4 1-1 1A9 9 0 0 1 1 2c0-.6.4-1 1-1z"/></svg>555-014-2276</li>
        <li><svg viewBox="0 0 12 12"><path d="M3 0h6a1 1 0 0 1 1 1v10a1 1 0 0 1-1 1H3a1 1 0 0 1-1-1V1a1 1 0 0 1 1-1zm0 2v7h6V2zm3 8a.6.6 0 1 0 0 1.2.6.6 0 0 0 0-1.2z"/></svg>555-018-3340</li>
        <li><svg viewBox="0 0 12 12"><path d="M6 0a6 6 0 1 0 0 12A6 6 0 0 0 6 0zm0 1.2c.7 0 1.5 1.5 1.7 3.8H4.3C4.5 2.7 5.3 1.2 6 1.2zM1.3 5h1.8c.1-1.4.4-2.6.9-3.4A4.8 4.8 0 0 0 1.3 5zm0 2a4.8 4.8 0 0 0 2.7 3.4c-.5-.8-.8-2-.9-3.4zm3 0h3.4c-.2 2.3-1 3.8-1.7 3.8S4.5 9.3 4.3 7zm4.6 0c-.1 1.4-.4 2.6-.9 3.4A4.8 4.8 0 0 0 10.7 7zm1.8-2A4.8 4.8 0 0 0 8 1.6c.5.8.8 2 .9 3.4z"/></svg>dhartley@corvanerx.com</li>
        <li class="plain">180 Meridian Avenue</li>
        <li class="plain">Brookfield, OH 44403</li>
      </ul>
    </div>
  </section>
</body>
</html>
```